Retail Jewelry Business Card Design Project

We are in need of a new business card design for a retail jewelry store. This store is in the business of fine jewelry including but not specific to bridal jewelry, diamonds, designer jewelry and watches.

This store has been in business for 20 years but continues to strive for a modern professional appeal. The main colors use for this business are a royal blue, white and silver.

Target Market(s)

Target market is ages 18-50

Industry/Entity Type

Jewelry

Requirements
Must have
• Sales Person Name
Sales Person Email Address

Store Address
Store Phone
Website

Standard business card size. No odd shapes or sizes.
Nice to have
• Overall modern feel for card.

We have thought that a design with a nice feature of the logo on the back of the card would be nice but open to ideas.
Should not have
• No specific images of jewelry should be used.

```html
<!DOCTYPE html>
<html lang="en">
<head>
<meta charset="utf-8">
<title>Marlow Reed Fine Jewelry – Business Card</title>
<link href="https://fonts.googleapis.com/css2?family=Open+Sans:wght@400;600&display=swap" rel="stylesheet">
<style>
  :root {
    --royal-blue: #2e3192;
    --lavender: #7470b4;
    --white: #ffffff;
    --ink: #3a3a3a;
    --stage: #e8e5e1;
    --label: #222222;
  }
  * { box-sizing: border-box; margin: 0; padding: 0; }
  html, body {
    width: 1200px; height: 788px; overflow: hidden;
    background: var(--stage);
    font-family: "Open Sans", Arial, sans-serif;
  }
  .sheet { position: relative; width: 1200px; height: 788px; }
  .side-label {
    position: absolute; width: 525px; text-align: center;
    font-size: 21px; color: var(--label); line-height: 1;
  }
  .card {
    position: absolute; width: 525px; height: 300px;
    border-radius: 22px; overflow: hidden;
  }
  .card--white { background: var(--white); }
  .card--blue { background: var(--royal-blue); }
  .card--lavender { background: var(--lavender); }

  .pos-a { left: 54px; }
  .pos-b { left: 622px; }
  .row-1 { top: 74px; }
  .row-2 { top: 445px; }
  .label-row-1 { top: 36px; }
  .label-row-2 { top: 407px; }

  /* Front */
  .front-name {
    position: absolute; left: 22px; top: 96px; width: 228px;
    text-align: center; color: var(--royal-blue);
    font-weight: 600; font-size: 25px; line-height: 1.2;
  }
  .front-divider {
    position: absolute; left: 274px; top: 74px;
    width: 1px; height: 118px; background: #9a9a9a;
  }
  .contact-list {
    position: absolute; left: 298px; top: 74px;
    list-style: none; font-size: 13px; color: var(--ink); line-height: 1.35;
  }
  .contact-item { display: flex; align-items: flex-start; margin-bottom: 6px; }
  .contact-item svg { width: 12px; height: 12px; margin: 3px 6px 0 0; flex: none; fill: var(--ink); }
  .front-band { position: absolute; left: 0; top: 0; width: 525px; height: 300px; }
  .holder-name {
    position: absolute; left: 273px; top: 264px;
    font-size: 16px; color: var(--white);
  }

  /* Backs */
  .back-name {
    position: absolute; left: 0; top: 70px; width: 100%;
    text-align: center; font-weight: 600; font-size: 44px; line-height: 1.15;
  }
  .back-name--blue { color: var(--royal-blue); }
  .back-name--white { color: var(--white); }
  .back-web {
    position: absolute; left: 0; top: 258px; width: 100%;
    text-align: center; font-size: 13px; letter-spacing: 1.6px;
  }
  .back-web--blue { color: var(--royal-blue); }
  .back-web--white { color: var(--white); }
  .back-web--dark { color: #1f1f4a; }
</style>
</head>
<body>
<main class="sheet">

  <p class="side-label pos-a label-row-1">Front</p>
  <section class="card card--white pos-a row-1">
    <svg class="front-band" viewBox="0 0 525 300" aria-hidden="true">
      <path d="M0,270 C110,258 230,251 330,249 C220,256 100,276 0,292 Z" fill="var(--lavender)"/>
      <path d="M0,300 L0,298 C140,273 260,255 360,250 C440,247 500,251 525,262 L525,300 Z" fill="var(--royal-blue)"/>
    </svg>
    <h1 class="front-name">Marlow Reed<br>Fine Jewelry</h1>
    <div class="front-divider"></div>
    <ul class="contact-list">
      <li class="contact-item">
        <svg viewBox="0 0 12 12"><path d="M2.5 0.5 L4.5 0.5 L5.2 3.2 L3.8 4.3 C4.5 5.8 6.2 7.5 7.7 8.2 L8.8 6.8 L11.5 7.5 L11.5 9.5 C11.5 10.8 10.5 11.5 9.5 11.5 C4.5 11 1 7.5 0.5 2.5 C0.5 1.5 1.2 0.5 2.5 0.5 Z"/></svg>
        <span>555-218-4470</span>
      </li>
      <li class="contact-item">
        <svg viewBox="0 0 12 12"><path d="M0.5 2.5 H11.5 V10 H0.5 Z M0.5 2.5 L6 6.8 L11.5 2.5" fill="none" stroke="var(--ink)" stroke-width="1.3"/></svg>
        <span>marlow@marlowreedjewelry.com</span>
      </li>
      <li class="contact-item">
        <svg viewBox="0 0 12 12"><g fill="none" stroke="var(--ink)" stroke-width="1.1"><circle cx="6" cy="6" r="5.2"/><ellipse cx="6" cy="6" rx="2.3" ry="5.2"/><path d="M0.8 6 H11.2 M1.8 3.3 H10.2 M1.8 8.7 H10.2"/></g></svg>
        <span>www.marlowreedjewelry.com</span>
      </li>
      <li class="contact-item">
        <svg viewBox="0 0 12 12"><path d="M6 0.8 L11.5 5.8 L10 5.8 L10 11.2 L7.3 11.2 L7.3 7.8 L4.7 7.8 L4.7 11.2 L2 11.2 L2 5.8 L0.5 5.8 Z"/></svg>
        <span>2208 Linden Avenue<br>Harbor Point, FL 32409</span>
      </li>
    </ul>
    <p class="holder-name">Marlow Reed Ashford</p>
  </section>

  <p class="side-label pos-b label-row-1">Back - 1</p>
  <section class="card card--white pos-b row-1">
    <h2 class="back-name back-name--blue">Marlow Reed<br>Fine Jewelry</h2>
    <p class="back-web back-web--blue">www.marlowreedjewelry.com</p>
  </section>

  <p class="side-label pos-a label-row-2">Back - 2</p>
  <section class="card card--blue pos-a row-2">
    <h2 class="back-name back-name--white">Marlow Reed<br>Fine Jewelry</h2>
    <p class="back-web back-web--white">www.marlowreedjewelry.com</p>
  </section>

  <p class="side-label pos-b label-row-2">Back - 3</p>
  <section class="card card--lavender pos-b row-2">
    <h2 class="back-name back-name--blue">Marlow Reed<br>Fine Jewelry</h2>
    <p class="back-web back-web--dark">www.marlowreedjewelry.com</p>
  </section>

</main>
</body>
</html>
```